Foot doctor needs feet friendly business cards.

Business cards for Podiatrist. Needs to look professional and modern. Back side put an appointment card, and try to put a little basic street map somewhere on card along with all of our contact info below:

Marcus Dovan, DPM, Inc.
Diplomate, National Council of Lower Limb Medicine
Call: 1.877.Toes.482
1.555.283.9146
Fax: 1.555.671.3820
Email: info@DrDovanclinic.example
Web: www.DrDovanclinic.example
2847 W. Harbor Ln. Suite 204
Lindenport, CA 90000

```html
<!DOCTYPE html>
<html lang="en">
<head>
<meta charset="utf-8">
<title>Marcus Dovan, DPM, Inc. – Business Card</title>
<link rel="stylesheet" href="https://fonts.googleapis.com/css2?family=Lato:wght@400;700;900&display=swap">
<style>
  :root {
    --paper: #ffffff;
    --brand-orange: #ef5a24;
    --emblem-blue: #2aa3d6;
    --feet-white: #ffffff;
    --ink: #333333;
    --ink-soft: #555555;
    --rule: #3a3a3a;
    --side-band: #333333;
  }
  html, body {
    margin: 0;
    padding: 0;
    width: 1200px;
    height: 720px;
    overflow: hidden;
    background: var(--paper);
  }
  .card {
    position: relative;
    width: 1200px;
    height: 720px;
    background: var(--paper);
    font-family: "Lato", Arial, sans-serif;
    color: var(--ink);
    overflow: hidden;
  }
  .brand-panel {
    position: absolute;
    left: 80px;
    top: 0;
    width: 400px;
    height: 720px;
    background: var(--brand-orange);
  }
  .emblem {
    position: absolute;
    left: 133px;
    top: 59px;
    width: 300px;
    height: 282px;
    border-radius: 40px 40px 150px 150px;
    background: var(--emblem-blue);
  }
  .feet {
    position: absolute;
    left: 153px;
    top: 411px;
    width: 250px;
    height: 234px;
    border-radius: 60px;
    background: var(--feet-white);
  }
  .side-band {
    position: absolute;
    right: 0;
    top: 0;
    width: 80px;
    height: 720px;
    background: var(--side-band);
  }
  .doctor-name {
    position: absolute;
    left: 526px;
    top: 36px;
    margin: 0;
    font-size: 70px;
    line-height: 1;
    font-weight: 900;
    letter-spacing: -2px;
    color: var(--ink);
    white-space: nowrap;
  }
  .doctor-name .surname { font-weight: 400; }
  .practice-suffix {
    position: absolute;
    right: 234px;
    top: 104px;
    margin: 0;
    font-size: 31px;
    line-height: 1;
    font-weight: 400;
    color: var(--ink);
  }
  .credential {
    position: absolute;
    left: 480px;
    width: 640px;
    top: 156px;
    margin: 0;
    text-align: center;
    font-size: 21px;
    font-weight: 700;
    color: var(--ink-soft);
    white-space: nowrap;
  }
  .rule {
    position: absolute;
    left: 523px;
    width: 554px;
    height: 2px;
    background: var(--rule);
  }
  .rule--top { top: 228px; }
  .rule--bottom { top: 341px; }
  .specialties {
    position: absolute;
    left: 523px;
    width: 554px;
    top: 240px;
    margin: 0;
    padding: 0;
    list-style: none;
    text-align: center;
    font-size: 33px;
    line-height: 41px;
    font-weight: 900;
    color: var(--ink);
    letter-spacing: -0.3px;
    white-space: nowrap;
  }
  .contact-row {
    position: absolute;
    left: 545px;
    display: flex;
    align-items: center;
  }
  .contact-row .icon {
    width: 30px;
    height: 26px;
    fill: var(--ink);
    flex: none;
  }
  .contact-row .value {
    position: absolute;
    left: 72px;
    font-size: 22px;
    line-height: 32px;
    font-weight: 700;
    color: var(--ink);
    white-space: nowrap;
  }
  .row-phone { top: 382px; }
  .row-phone .value { top: -13px; line-height: 31px; }
  .row-fax { top: 455px; }
  .row-fax .value { top: -3px; }
  .row-email { top: 502px; }
  .row-email .value { top: -3px; }
  .row-web { top: 538px; }
  .row-web .value { top: -4px; }
  .row-address { top: 594px; }
  .row-address .value { top: -17px; }
</style>
</head>
<body>
<div class="card">
  <div class="brand-panel"></div>
  <div class="emblem" role="img" aria-label="Blue winged caduceus medical emblem"></div>
  <div class="feet" role="img" aria-label="Pair of white footprints"></div>
  <div class="side-band"></div>

  <h1 class="doctor-name">MARCUS <span class="surname">DOVAN</span></h1>
  <p class="practice-suffix">DPM, Inc.</p>
  <p class="credential">DIPLOMAT, NATIONAL COUNCIL OF LOWER LIMB MEDICINE</p>

  <div class="rule rule--top"></div>
  <ul class="specialties">
    <li>NAIL FUNGUS LASER TREATMENTS</li>
    <li>HEEL PAIN RELIEF SPECIALIST</li>
  </ul>
  <div class="rule rule--bottom"></div>

  <div class="contact-row row-phone">
    <svg class="icon" viewBox="0 0 30 26" aria-hidden="true">
      <path d="M2 8c0-4 6-6 13-6s13 2 13 6v2h-6V7.5c-2-.8-4.5-1.2-7-1.2s-5 .4-7 1.2V10H2z"/>
      <path d="M7 11h16l4 8v6H3v-6z M11 13v2h2v-2z M14 13v2h2v-2z M17 13v2h2v-2z M11 16v2h2v-2z M14 16v2h2v-2z M17 16v2h2v-2z" fill-rule="evenodd"/>
    </svg>
    <div class="value">1 877 863 7482<br>1.555.283.9146</div>
  </div>

  <div class="contact-row row-fax">
    <svg class="icon" viewBox="0 0 30 26" aria-hidden="true">
      <rect x="8" y="1" width="14" height="7"/>
      <path d="M2 9h26v11h-5v-5H7v5H2z"/>
      <rect x="9" y="17" width="12" height="8"/>
    </svg>
    <div class="value">1.555.671.3820</div>
  </div>

  <div class="contact-row row-email">
    <svg class="icon" viewBox="0 0 30 26" aria-hidden="true">
      <path d="M2 3h26v20H2z M4.5 5.5v15h21v-15z M5 6l10 9 10-9v2.5l-10 9-10-9z" fill-rule="evenodd"/>
    </svg>
    <div class="value">info@DrDovanclinic.example</div>
  </div>

  <div class="contact-row row-web">
    <svg class="icon" viewBox="0 0 30 26" aria-hidden="true">
      <path d="M2 2h26v17H2z M4.5 4.5v12h21v-12z" fill-rule="evenodd"/>
      <rect x="13" y="19" width="4" height="3"/>
      <rect x="8" y="22" width="14" height="2.5"/>
    </svg>
    <div class="value">www.DrDovanclinic.example</div>
  </div>

  <div class="contact-row row-address">
    <svg class="icon" viewBox="0 0 30 26" aria-hidden="true">
      <path d="M15 2L1 14h4v11h8v-7h4v7h8V14h4z"/>
    </svg>
    <div class="value">2847 W. Harbor Ln. Suite 204<br>Lindenport, CA 90000</div>
  </div>
</div>
</body>
</html>
```